Kestrel Facilities Business Card Design

We would now like to design business cards with the new Kestrel Facilities logo

Target Market(s)

Professional

Industry/Entity Type

Professional services

Contact Information for Business Card

Employee name, title, phone number, email address, corporate office address and logo.

Font styles to use
Sans Serif

Colors
0054AA
0677BA
7BADD7
CADEEF
E8F1F8

Requirements
Must have
• My logo
Should not have
• any other pictures or images besides my logo

```html
<!DOCTYPE html>
<html lang="en">
<head>
<meta charset="utf-8">
<title>Kestrel Facilities Business Card</title>
<link href="https://fonts.googleapis.com/css2?family=Montserrat:wght@400;500;700&display=swap" rel="stylesheet">
<style>
  :root {
    --brand-blue: #3578be;
    --ink: #1f1f1f;
    --paper: #ffffff;
    --backdrop: #9c9c9c;
    --swoosh-dark: #2b2b2b;
  }
  * { margin: 0; padding: 0; box-sizing: border-box; }
  html, body { width: 1200px; height: 900px; overflow: hidden; }
  body {
    background: var(--backdrop);
    font-family: "Montserrat", sans-serif;
    position: relative;
  }
  .card {
    position: absolute;
    width: 560px;
    height: 320px;
    border-radius: 26px;
    overflow: hidden;
    box-shadow: 0 6px 18px rgba(0,0,0,0.25);
  }
  .card--front {
    left: 60px; top: 90px;
    background: var(--brand-blue);
    display: flex; align-items: center; justify-content: center;
  }
  .card--back {
    left: 580px; top: 490px;
    background: var(--paper);
  }
  .brand {
    display: flex; align-items: center; gap: 14px;
    font-weight: 500;
    letter-spacing: 0.04em;
    text-transform: uppercase;
  }
  .brand__mark { width: 30px; height: 30px; }
  .card--front .brand { color: var(--paper); font-size: 34px; }
  .card--front .brand__mark { background: var(--paper); width: 34px; height: 34px; }
  .card--back .brand {
    position: absolute; left: 40px; top: 112px;
    color: var(--brand-blue); font-size: 22px; line-height: 1.15;
  }
  .card--back .brand__mark { background: var(--brand-blue); }
  .divider {
    position: absolute; left: 268px; top: 48px;
    width: 2px; height: 170px; background: var(--brand-blue);
  }
  .contact {
    position: absolute; left: 290px; top: 40px;
    color: var(--ink);
  }
  .contact__name { color: var(--brand-blue); font-weight: 700; font-size: 21px; letter-spacing: 0.01em; }
  .contact__title { font-size: 13px; margin-top: 2px; }
  .contact__address { font-size: 12px; margin-top: 12px; line-height: 1.35; }
  .contact__list { list-style: none; margin-top: 10px; font-size: 12.5px; }
  .contact__list li { display: flex; align-items: center; gap: 7px; margin-top: 3px; }
  .contact__list svg { width: 13px; height: 13px; fill: var(--brand-blue); flex: none; }
  .swoosh { position: absolute; left: 0; bottom: 0; width: 560px; height: 140px; }
</style>
</head>
<body>
  <section class="card card--front" aria-label="Card front">
    <div class="brand"><span class="brand__mark"></span><span>Kestrel<br>Facilities</span></div>
  </section>

  <section class="card card--back" aria-label="Card back">
    <div class="brand"><span class="brand__mark"></span><span>Kestrel<br>Facilities</span></div>
    <div class="divider"></div>
    <div class="contact">
      <p class="contact__name">MUMBI KARIUKI</p>
      <p class="contact__title">Co-Founder</p>
      <p class="contact__address">P.O Box 4410-00100<br>Nairobi, Kenya</p>
      <ul class="contact__list">
        <li><svg viewBox="0 0 16 16"><path d="M3 1h3l1.5 4-2 1.3a9 9 0 0 0 4.2 4.2L11 8.5l4 1.5v3a2 2 0 0 1-2 2A12 12 0 0 1 1 3a2 2 0 0 1 2-2z"/></svg>+254-700-55012</li>
        <li><svg viewBox="0 0 16 16"><path d="M1 3h14v10H1z M1 3l7 6 7-6" fill="none" stroke="#3578be" stroke-width="1.6"/></svg>info@kestrelfacilities.com</li>
        <li><svg viewBox="0 0 16 16"><circle cx="8" cy="8" r="6.5" fill="none" stroke="#3578be" stroke-width="1.5"/><path d="M1.5 8h13M8 1.5c-3 3.5-3 9.5 0 13M8 1.5c3 3.5 3 9.5 0 13" fill="none" stroke="#3578be" stroke-width="1.2"/></svg>www.kestrelfacilities.com</li>
      </ul>
    </div>
    <svg class="swoosh" viewBox="0 0 560 140" preserveAspectRatio="none" aria-hidden="true">
      <path d="M0 140 L0 125 C180 120 380 70 560 0 L560 140 Z" fill="var(--brand-blue)"/>
      <path d="M150 118 C300 95 430 50 560 0 L560 8 C430 56 300 100 150 118 Z" fill="var(--swoosh-dark)"/>
    </svg>
  </section>
</body>
</html>
```